Upscale business cards needed for Board of Directors

We need professional business cards created for members of our family business Board of Directors. We would like these relatively simple and straightforward, but also with a unique element to set them apart. Probably stick with neutral and simple colors - white, grey etc. We need space for the traditional elements, including name, title, address, email/phone number. And we will be creating several from this template so it needs to be template that is easy to switch information in and out of.
Business
See description

```html
<!DOCTYPE html>
<html lang="en">
<head>
<meta charset="utf-8">
<title>Harbourline Holdings – Business Card</title>
<link href="https://fonts.googleapis.com/css2?family=Lato:wght@400;700;900&display=swap" rel="stylesheet">
<style>
  :root {
    --gold: #b19f73;
    --ink: #111111;
    --paper: #ffffff;
    --backdrop: #2e2e2e;
  }
  * { margin: 0; padding: 0; box-sizing: border-box; }
  html, body { width: 1200px; height: 900px; overflow: hidden; }
  body {
    background: var(--backdrop);
    font-family: 'Lato', Arial, sans-serif;
    position: relative;
  }
  .card {
    position: absolute;
    width: 600px;
    height: 343px;
    overflow: hidden;
    box-shadow: 0 10px 30px rgba(0,0,0,0.45);
  }
  /* Back of card */
  .card-back {
    left: 540px;
    top: 90px;
    background: var(--gold);
  }
  .card-back .brand {
    position: absolute;
    left: 0; right: 0;
    top: 118px;
    text-align: center;
    color: var(--ink);
    font-weight: 900;
    font-size: 40px;
    letter-spacing: 2px;
    line-height: 1;
    text-transform: uppercase;
  }
  .card-back .brand-sub {
    position: absolute;
    left: 0; right: 0;
    top: 166px;
    text-align: center;
    color: var(--ink);
    font-weight: 900;
    font-size: 20px;
    letter-spacing: 12px;
    text-transform: uppercase;
  }
  .card-back .web {
    position: absolute;
    left: 0; right: 0;
    bottom: 40px;
    text-align: center;
    color: var(--paper);
    font-size: 15px;
    letter-spacing: 2px;
  }
  /* Front of card */
  .card-front {
    left: 60px;
    top: 470px;
    background: var(--paper);
  }
  .card-front .wave { position: absolute; inset: 0; }
  .card-front .brand {
    position: absolute;
    left: 36px;
    top: 34px;
    color: var(--ink);
    font-weight: 900;
    font-size: 32px;
    letter-spacing: 1.5px;
    line-height: 1;
    text-transform: uppercase;
  }
  .card-front .brand-sub {
    position: absolute;
    left: 36px;
    top: 72px;
    color: var(--ink);
    font-weight: 900;
    font-size: 16px;
    letter-spacing: 10px;
    text-transform: uppercase;
  }
  .contact-list {
    position: absolute;
    left: 38px;
    top: 130px;
    list-style: none;
    font-size: 13px;
    color: var(--ink);
  }
  .contact-list li {
    display: flex;
    align-items: center;
    gap: 8px;
    height: 19px;
  }
  .contact-list svg { width: 11px; height: 11px; fill: var(--gold); }
  .holder {
    position: absolute;
    right: 46px;
    top: 160px;
    text-align: right;
    color: var(--ink);
  }
  .holder .name { font-size: 22px; font-weight: 400; }
  .holder .role { font-size: 15px; color: var(--gold); margin-top: 2px; }
  .holder .address { font-size: 15px; margin-top: 10px; line-height: 1.25; }
  .card-front .web {
    position: absolute;
    left: 250px;
    bottom: 12px;
    color: var(--paper);
    font-size: 17px;
    letter-spacing: 1px;
  }
</style>
</head>
<body>

  <section class="card card-back">
    <div class="brand">Harbourline</div>
    <div class="brand-sub">Holdings</div>
    <div class="web">www.harbourline.com</div>
  </section>

  <section class="card card-front">
    <svg class="wave" viewBox="0 0 600 343" preserveAspectRatio="none" aria-hidden="true">
      <path fill="var(--ink)" d="M0,222 C130,230 220,280 340,284 C450,288 540,276 600,266 L600,343 L0,343 Z"/>
      <path fill="var(--paper)" d="M0,238 C140,247 225,292 340,296 C450,299 540,288 600,278 L600,343 L0,343 Z"/>
      <path fill="var(--gold)" d="M0,244 C145,254 228,298 340,302 C450,305 540,294 600,284 L600,343 L0,343 Z"/>
    </svg>

    <div class="brand">Harbourline</div>
    <div class="brand-sub">Holdings</div>

    <ul class="contact-list">
      <li>
        <svg viewBox="0 0 12 12"><path d="M2.5 1 L4.5 1 L5.2 3.6 L4 4.6 C4.6 6 6 7.4 7.4 8 L8.4 6.8 L11 7.5 L11 9.5 C11 10.3 10.3 11 9.5 11 C5 11 1 7 1 2.5 C1 1.7 1.7 1 2.5 1 Z"/></svg>
        555 014 2200
      </li>
      <li>
        <svg viewBox="0 0 12 12"><path d="M3 1 H9 V4 H3 Z M1 4.5 H11 V9 H9 V11 H3 V9 H1 Z M4 8 V10 H8 V8 Z"/></svg>
        555 014 2201
      </li>
      <li>
        <svg viewBox="0 0 12 12"><path d="M1 2.5 H11 V9.5 H1 Z M1.6 3.2 L6 6.6 L10.4 3.2 Z" fill-rule="evenodd"/></svg>
        info@harbourline.com
      </li>
    </ul>

    <div class="holder">
      <div class="name">Daniel Whitford</div>
      <div class="role">Director</div>
      <div class="address">4100 Elm Ridge Road<br>Marlow TX 78010</div>
    </div>

    <div class="web">www.harbourline.com</div>
  </section>

</body>
</html>
```